Graphic designs required for HR consulting Website

We need to items designed to be used on our website and in presentations.
Please view our website for design ideas.
http://www.brightmoor.com.au.42.vexaloft.pw
See attached Powerpoint doc for more info.
InfoGraphic 1
Needs to be turned into an infographic that will be embedded into the Brightmoor HR website.
The fonts should be Helvetica Neue and should have the look and feel of the website.
InfoGraphic 2
Needs to be turned into an infographic that will be embedded into the Brightmoor HR website and used in PPT and WORD proposals.
The fonts should be Helvetica Neue, the look and
feel should be consistent with the first infographic.
A mountain analogy is needed that shows how the sequence of services will come together to take businesses on the journey to becoming great.
2 versions of the same information are shown on the following slides. The first is for ease of visibility, the second is to show the sequence of services on the journey.
Samples of possible design ideas for inspiration are at bottom of ppt.
Consulting
- Helvetica

```html
<!DOCTYPE html>
<html lang="en">
<head>
<meta charset="utf-8">
<title>Brightmoor – People &amp; Performance Services</title>
<link href="https://fonts.googleapis.com/css2?family=Inter:wght@300;400&display=swap" rel="stylesheet">
<style>
  :root {
    --page: #ffffff;
    --canvas: #eefafb;
    --ink: #1b1b1b;
    --brand-blue: #1d8ce0;
    --link-blue: #3a8ef0;
    --dot-blue: #1f7fd0;
  }
  html, body {
    margin: 0;
    padding: 0;
    width: 1200px;
    height: 946px;
    overflow: hidden;
    background: var(--page);
  }
  .infographic {
    position: relative;
    width: 1188px;
    height: 934px;
    margin: 6px;
    background: var(--canvas);
    font-family: "Inter", "Helvetica Neue", Arial, sans-serif;
    font-weight: 300;
    color: var(--ink);
  }
  .title {
    position: absolute;
    left: 55px;
    top: 58px;
    margin: 0;
    font-size: 44px;
    font-weight: 300;
    color: var(--brand-blue);
    letter-spacing: -0.5px;
  }
  .column-head {
    position: absolute;
    margin: 0;
    font-size: 35px;
    font-weight: 300;
    line-height: 34px;
    letter-spacing: -0.6px;
  }
  .column-head.needs { left: 55px; top: 162px; }
  .column-head.help { right: 52px; top: 180px; text-align: right; }
  .row-label {
    position: absolute;
    left: 55px;
    margin: 0;
    font-size: 33px;
    font-weight: 300;
    letter-spacing: -0.5px;
  }
  .card {
    position: absolute;
    width: 466px;
    height: 119px;
  }
  .card svg {
    position: absolute;
    left: 0; top: 0;
    overflow: visible;
  }
  .card.need { left: 56px; }
  .card.service { left: 669px; }
  .card-text {
    position: absolute;
    top: 0;
    height: 119px;
    display: flex;
    flex-direction: column;
    justify-content: center;
    font-size: 18px;
    line-height: 19.5px;
    letter-spacing: -0.4px;
  }
  .need .card-text { left: 147px; right: 8px; }
  .service .card-text { left: 34px; right: 136px; font-size: 18px; line-height: 17px; }
  .service .card-text.compact { font-size: 16px; line-height: 16px; letter-spacing: -0.5px; }
  .service-name {
    font-size: 25px;
    line-height: 24px;
    color: var(--link-blue);
    letter-spacing: -0.5px;
    white-space: nowrap;
  }
  .connector { position: absolute; left: 548px; }
</style>
</head>
<body>
<svg width="0" height="0" style="position:absolute" aria-hidden="true">
  <defs>
    <linearGradient id="blue-band" x1="0" y1="0" x2="1" y2="0">
      <stop offset="0" stop-color="#0f86d8"/>
      <stop offset="0.55" stop-color="#2fa9ec"/>
      <stop offset="1" stop-color="#0d78c8"/>
    </linearGradient>
    <linearGradient id="grey-panel" x1="0" y1="0" x2="1" y2="0">
      <stop offset="0" stop-color="#ffffff"/>
      <stop offset="0.55" stop-color="#e2e3e6"/>
      <stop offset="1" stop-color="#a9aab0"/>
    </linearGradient>
    <radialGradient id="ring" cx="0.4" cy="0.35" r="0.7">
      <stop offset="0" stop-color="#ffffff"/>
      <stop offset="0.7" stop-color="#e6e7ea"/>
      <stop offset="1" stop-color="#a6a8ad"/>
    </radialGradient>
    <radialGradient id="button" cx="0.4" cy="0.3" r="0.75">
      <stop offset="0" stop-color="#4fc0f6"/>
      <stop offset="1" stop-color="#0b7fd4"/>
    </radialGradient>
    <filter id="card-shadow" x="-10%" y="-10%" width="120%" height="130%">
      <feDropShadow dx="0" dy="4" stdDeviation="4" flood-color="#000" flood-opacity="0.28"/>
    </filter>
    <g id="card-shape">
      <path d="M0,0 H120 V119 H62 A62,57 0 0 1 0,62 Z" fill="url(#blue-band)"/>
      <path d="M0,0 H16 V80 Q16,119 56,119 H40 A40,40 0 0 1 0,79 Z" fill="#0a6fbd" opacity="0.35"/>
      <path d="M96,119 V72 A72,72 0 0 1 168,0 H420 A46,46 0 0 1 466,46 V119 Z" fill="url(#grey-panel)" filter="url(#card-shadow)"/>
      <circle cx="96" cy="66" r="37" fill="url(#ring)" filter="url(#card-shadow)"/>
      <circle cx="96" cy="66" r="24" fill="url(#button)" stroke="#ffffff" stroke-width="1.5"/>
    </g>
    <path id="icon-play" d="M-7,-11 L12,0 L-7,11 Z" fill="#ffffff"/>
    <path id="icon-up" d="M0,-11 L12,9 L-12,9 Z" fill="#ffffff"/>
    <path id="icon-star" d="M0,-12 L3.5,-4 L12,-3.7 L5.4,1.8 L7.6,10 L0,5.4 L-7.6,10 L-5.4,1.8 L-12,-3.7 L-3.5,-4 Z" fill="#ffffff"/>
    <g id="dotted-arrow">
      <circle cx="9" cy="9" r="9" fill="var(--dot-blue)"/>
      <path d="M26,9 H90" stroke="var(--dot-blue)" stroke-width="4" stroke-dasharray="10 8"/>
      <path d="M92,0 L104,9 L92,18 L96,9 Z" fill="var(--dot-blue)"/>
    </g>
  </defs>
</svg>

<main class="infographic">
  <h1 class="title">Infographic 1</h1>
  <h2 class="column-head needs">The people &amp; performance<br>needs of every business</h2>
  <h2 class="column-head help">How we can help you</h2>

  <h3 class="row-label" style="top:282px">Compliance</h3>
  <div class="card need" style="top:329px">
    <svg width="466" height="119" viewBox="0 0 466 119" aria-hidden="true">
      <use href="#card-shape"/>
      <use href="#icon-play" x="98" y="66"/>
    </svg>
    <div class="card-text">Trusted advice on people issues including Fair Work Act compliance, redundancies, performance management, terminations, policies and safety.</div>
  </div>
  <svg class="connector" style="top:379px" width="106" height="18" viewBox="0 0 106 18" aria-hidden="true"><use href="#dotted-arrow"/></svg>
  <div class="card service" style="top:329px">
    <svg width="466" height="119" viewBox="0 0 466 119" aria-hidden="true">
      <g transform="translate(466,0) scale(-1,1)"><use href="#card-shape"/></g>
      <use href="#icon-play" x="370" y="66"/>
    </svg>
    <div class="card-text"><span class="service-name">HR On-Demand</span>Monthly subscription</div>
  </div>

  <h3 class="row-label" style="top:499px">HR Operations</h3>
  <div class="card need" style="top:546px">
    <svg width="466" height="119" viewBox="0 0 466 119" aria-hidden="true">
      <use href="#card-shape"/>
      <use href="#icon-up" x="96" y="66"/>
    </svg>
    <div class="card-text">Operational HR support including recruitment, performance management and training.</div>
  </div>
  <svg class="connector" style="top:601px" width="106" height="18" viewBox="0 0 106 18" aria-hidden="true"><use href="#dotted-arrow"/></svg>
  <div class="card service" style="top:546px">
    <svg width="466" height="119" viewBox="0 0 466 119" aria-hidden="true">
      <g transform="translate(466,0) scale(-1,1)"><use href="#card-shape"/></g>
      <use href="#icon-up" x="370" y="66"/>
    </svg>
    <div class="card-text compact"><span class="service-name">Onsite or Remote<br>HR Manager</span>Outsourced HR (annual subscription)<br>OR adhoc HR support (fixed fee<br>projects)</div>
  </div>

  <h3 class="row-label" style="top:716px">People &amp; Performance Strategy</h3>
  <div class="card need" style="top:764px">
    <svg width="466" height="119" viewBox="0 0 466 119" aria-hidden="true">
      <use href="#card-shape"/>
      <use href="#icon-star" x="96" y="66"/>
    </svg>
    <div class="card-text">Business strategy and planning, strategic HR frameworks and interventions to fuel your growth.</div>
  </div>
  <svg class="connector" style="top:817px" width="106" height="18" viewBox="0 0 106 18" aria-hidden="true"><use href="#dotted-arrow"/></svg>
  <div class="card service" style="top:764px">
    <svg width="466" height="119" viewBox="0 0 466 119" aria-hidden="true">
      <g transform="translate(466,0) scale(-1,1)"><use href="#card-shape"/></g>
      <use href="#icon-star" x="370" y="66"/>
    </svg>
    <div class="card-text"><span class="service-name">Strategic Expertise</span>Fixed fee project based expertise</div>
  </div>
</main>
</body>
</html>
```